I need an amazing business card!

I am the principle in my own software company that develops zorPad and mobile applications. I require a great business card design. I've attached my corporate logo (Thanks Tomas!).
I would like the design to integrate the logo, my name, email address and skype account:
name Brent Olafsen
email brentolafsen@tavrik.com
skype brentolafsen.net
I would like the back of the card to have a "write on me area" similar to the "write on me" card on this page, row 6:
http://us.prindlewick.com/design-templates/business-cards/#industry=Computing%20%26%20IT
As far as the rest - it's all you!
Updates
1) Please add an example telephone number as well.
Industry/Entity Type
Software
Look and feel
Each slider illustrates characteristics of the customer's brand and the style your logo design should communicate.

```html
<!DOCTYPE html>
<html lang="en">
<head>
<meta charset="utf-8">
<title>Tavrik — Business Card</title>
<link rel="stylesheet" href="https://fonts.googleapis.com/css2?family=Exo+2:wght@400;500;600&display=swap">
<style>
  :root {
    --backdrop: #2b2b2b;
    --leaf: #a5c24b;
    --leaf-dark: #8eab37;
    --paper: #ffffff;
    --paper-shade: #efefef;
    --ink: #3e3e3e;
    --ink-soft: #5a5a5a;
  }
  * { box-sizing: border-box; margin: 0; padding: 0; }
  html, body {
    width: 1200px; height: 857px; overflow: hidden;
    background: var(--backdrop);
    font-family: "Exo 2", sans-serif;
  }
  .stage {
    position: relative; width: 1200px; height: 857px;
    display: flex; justify-content: center; align-items: center; gap: 40px;
  }
  .card {
    position: relative; width: 366px; height: 640px; overflow: hidden;
    box-shadow: 0 10px 30px rgba(0,0,0,.45);
  }
  /* Front */
  .card--front { background: var(--paper); }
  .front-shade { position: absolute; inset: 0; }
  .brand {
    position: absolute; left: 0; right: 0; display: flex; flex-direction: column;
    align-items: center; gap: 16px;
  }
  .card--front .brand { top: 80px; }
  .brand__mark { width: 84px; height: 84px; background: var(--leaf); border-radius: 14px; }
  .brand__name {
    font-size: 20px; font-weight: 500; letter-spacing: 10px; padding-left: 10px;
    color: var(--leaf);
  }
  .person { position: absolute; left: 40px; right: 0; top: 292px; }
  .person__name {
    font-size: 27px; font-weight: 500; letter-spacing: 2px; color: var(--ink);
    text-transform: uppercase;
  }
  .person__title {
    margin-top: 6px; background: var(--leaf); color: var(--paper);
    font-size: 17px; font-weight: 500; letter-spacing: 1.5px; text-transform: uppercase;
    height: 32px; line-height: 32px; padding-left: 14px; margin-left: -14px;
  }
  .address {
    position: absolute; left: 40px; top: 390px;
    font-size: 16px; line-height: 22px; color: var(--ink); font-weight: 500;
  }
  .contacts {
    position: absolute; left: 40px; top: 470px; list-style: none;
    font-size: 13px; color: var(--ink-soft);
  }
  .contacts li { display: flex; align-items: center; gap: 10px; height: 24px; }
  .contacts svg { width: 14px; height: 14px; fill: var(--ink-soft); flex: none; }
  /* Back */
  .card--back { background: var(--leaf); }
  .card--back .brand { top: 230px; gap: 20px; }
  .card--back .brand__mark { width: 120px; height: 120px; background: var(--paper); border-radius: 20px; }
  .card--back .brand__name { color: var(--paper); font-size: 24px; letter-spacing: 14px; padding-left: 14px; }
</style>
</head>
<body>
<main class="stage">
  <section class="card card--front" aria-label="Card front">
    <svg class="front-shade" viewBox="0 0 366 640" preserveAspectRatio="none" aria-hidden="true">
      <polygon points="0,0 366,0 366,230 0,330" fill="var(--paper-shade)"/>
    </svg>
    <div class="brand">
      <div class="brand__mark"></div>
      <div class="brand__name">tavrik</div>
    </div>
    <div class="person">
      <h1 class="person__name">Brent Olafsen</h1>
      <p class="person__title">General Manager</p>
    </div>
    <p class="address">42 Harlow Road,<br>2nd building Street E.</p>
    <ul class="contacts">
      <li><svg viewBox="0 0 16 16"><path d="M4 1l2.5 3-1.5 2a9 9 0 0 0 5 5l2-1.5 3 2.5-1.5 2.5C7 15 1 9 1.5 2.5z"/></svg>012 555 0147</li>
      <li><svg viewBox="0 0 16 16"><path d="M4 0h8v16H4zM5.5 2v10h5V2zM7 13.5h2v1H7z"/></svg>012 555 0147</li>
      <li><svg viewBox="0 0 16 16"><path d="M4 0h8v16H4zM5.5 2v10h5V2zM7 13.5h2v1H7z"/></svg>012 555 0147</li>
      <li><svg viewBox="0 0 16 16"><path d="M0 3h16v10H0zM1.5 4.5L8 9l6.5-4.5v-.2H1.5z"/></svg>brentolafsen@tavrik.com</li>
      <li><svg viewBox="0 0 16 16"><path d="M8 0a8 8 0 1 0 0 16A8 8 0 0 0 8 0zm0 1.5c1 1 1.8 3 2 5.5H6c.2-2.5 1-4.5 2-5.5zM1.6 7a6.5 6.5 0 0 1 3.4-5c-.6 1.4-1 3.1-1.1 5zm10.5 0c-.1-1.9-.5-3.6-1.1-5a6.5 6.5 0 0 1 3.4 5zM1.6 9h2.3c.1 1.9.5 3.6 1.1 5a6.5 6.5 0 0 1-3.4-5zM6 9h4c-.2 2.5-1 4.5-2 5.5-1-1-1.8-3-2-5.5zm6.1 0h2.3a6.5 6.5 0 0 1-3.4 5c.6-1.4 1-3.1 1.1-5z"/></svg>www.brentolafsen.net</li>
    </ul>
  </section>

  <section class="card card--back" aria-label="Card back">
    <div class="brand">
      <div class="brand__mark"></div>
      <div class="brand__name">tavrik</div>
    </div>
  </section>
</main>
</body>
</html>
```